Hot Consulting firm collateral upgrade

We need a stationary design for our Oakland based consulting company called Talvora. We provide consulting expertise in KLT compliance for Medical Device, Pharmaceutical, and Biotech companies. We will be using the stationary for all of our marketing collateral. We want the design to convey professionalism and quality. You can find our company color scheme from our website talvora-advisory.com. I have included a copy of our current stationary that needs an upgrade.
Target Market(s)
Medical Device, Pharma, and Biotech companies
Industry/Entity Type
It Company
Look and feel

```html
<!DOCTYPE html>
<html lang="en">
<head>
<meta charset="utf-8">
<title>Talvora Stationery</title>
<link href="https://fonts.googleapis.com/css2?family=Questrial&display=swap" rel="stylesheet">
<style>
:root{
  --bg:#d9d9d9;
  --paper:#f4f4f4;
  --paper-white:#ffffff;
  --slate:#5a5a5a;
  --slate-dark:#4d4d4d;
  --blue:#1f4fa3;
  --ink:#3a3a3a;
  --muted:#6b6b6b;
  --silver:#c9c9c9;
}
*{margin:0;padding:0;box-sizing:border-box}
html,body{width:1200px;height:1000px;overflow:hidden}
body{background:var(--bg);font-family:"Questrial",sans-serif;color:var(--ink);position:relative}
.piece{position:absolute;overflow:hidden}
.wordmark{font-family:"Questrial",sans-serif;font-weight:400;letter-spacing:.5px;line-height:1;display:flex;align-items:center;gap:.18em}
.wordmark .dot{display:inline-block;width:.32em;height:.32em;border-radius:50%;background:var(--blue)}
.wave{position:absolute;left:0;bottom:0;width:100%}

/* Folder */
.folder{left:152px;top:42px;width:431px;height:558px;background:var(--slate);border-radius:4px}
.folder .spine{position:absolute;left:22px;top:0;width:3px;height:100%;background:var(--slate-dark)}
.folder .wordmark{position:absolute;left:182px;top:460px;font-size:40px;color:#fff}

/* Letterhead */
.letterhead{left:616px;top:62px;width:417px;height:538px;background:var(--paper-white)}
.letterhead .wordmark{position:absolute;left:37px;top:44px;font-size:24px;color:var(--ink)}
.contact{position:absolute;font-size:6px;line-height:8px;color:var(--muted)}
.contact .row{display:flex;align-items:center;gap:3px}
.icon{width:6px;height:6px;background:var(--blue);border-radius:1px;display:inline-block}
.letterhead .contact{left:297px;top:28px}
.letter-body{position:absolute;left:37px;top:184px;width:346px;font-size:5.6px;line-height:7px;color:var(--muted);text-align:justify}
.letter-body p{margin-bottom:7px}
.letter-body .salute{font-weight:700;color:var(--ink)}
.signoff{position:absolute;left:37px;top:350px;font-size:5.6px;line-height:7px;color:var(--muted)}
.signoff strong{color:var(--ink)}
.signature{position:absolute;left:92px;top:346px;width:84px;height:40px;background:linear-gradient(90deg,rgba(31,79,163,.08),rgba(31,79,163,.16));border-radius:3px}

/* Envelope front */
.envelope-front{left:117px;top:630px;width:466px;height:201px;background:var(--paper)}
.envelope-front .wordmark{position:absolute;left:22px;top:32px;font-size:23px;color:var(--ink)}
.envelope-front .address{position:absolute;left:22px;top:60px;font-size:6px;line-height:7.5px;color:var(--muted)}

/* Envelope back */
.envelope-back{left:616px;top:630px;width:466px;height:201px;background:var(--paper-white)}
.envelope-back .flap{position:absolute;left:0;top:0;width:100%;height:110px}
.envelope-back .wordmark{position:absolute;left:212px;top:36px;font-size:11px;color:var(--blue)}

/* Business cards */
.card-back{left:410px;top:860px;width:173px;height:100px;background:var(--slate)}
.card-back .wordmark{position:absolute;left:84px;top:66px;font-size:15px;color:#fff}
.card-front{left:616px;top:860px;width:173px;height:100px;background:var(--paper-white)}
.card-front .wordmark{position:absolute;left:16px;top:26px;font-size:14px;color:var(--ink)}
.card-front .hq{position:absolute;left:16px;top:46px;font-size:4.3px;line-height:5.4px;color:var(--muted);text-align:right;width:60px}
.card-front .divider{position:absolute;left:94px;top:28px;width:1px;height:44px;background:var(--silver)}
.card-front .person{position:absolute;left:100px;top:31px}
.person .name{font-size:5.6px;color:var(--blue);font-weight:700;letter-spacing:.3px}
.person .role{font-size:4.5px;color:var(--muted);margin-bottom:5px}
.card-front .contact{position:static;font-size:4.3px;line-height:5.6px}
.card-front .icon{width:4px;height:4px}
</style>
</head>
<body>

<section class="piece folder" aria-label="Presentation folder">
  <div class="spine"></div>
  <div class="wordmark">talvora<span class="dot"></span></div>
</section>

<section class="piece letterhead" aria-label="Letterhead">
  <div class="wordmark">talvora<span class="dot"></span></div>
  <div class="contact">
    <div class="row"><span class="icon"></span>(415) 555-0142</div>
    <div class="row"><span class="icon"></span>info@talvora-advisory.com</div>
    <div class="row"><span class="icon"></span>www.talvora-advisory.com</div>
    <div style="margin-top:4px">Bay Area HQ</div>
    <div>2140 Harbor Way- Suite 310</div>
    <div>Oakland, CA 94607</div>
  </div>
  <div class="letter-body">
    <p class="salute">Dear sir,</p>
    <p>Thank you for considering Talvora as your compliance partner. Our team helps medical device, pharmaceutical and biotech companies prepare for audits, build quality systems and meet every KLT requirement with confidence and clarity.</p>
    <p>We begin with a careful review of your current processes, then agree on a clear plan with milestones, owners and timelines. Each step is documented so your team can keep the work going long after our engagement ends.</p>
    <p>Our consultants have guided many products from early design to market release. We know how reviewers think, and we share that insight so your submissions are complete, consistent and ready the first time.</p>
    <p>We would welcome the chance to discuss your goals. Please contact our office to arrange a meeting at a time that suits you.</p>
  </div>
  <div class="signoff">Yours Sincerely,<br><strong>Daniel Okafor</strong></div>
  <div class="signature" role="img" aria-label="Handwritten signature of Daniel Okafor"></div>
  <svg class="wave" viewBox="0 0 417 30" height="30" preserveAspectRatio="none">
    <path d="M0 12 C120 -2 260 0 417 18 L417 30 L0 30Z" fill="var(--blue)"/>
    <path d="M0 20 C130 6 270 8 417 22 L417 30 L0 30Z" fill="var(--silver)"/>
    <path d="M0 26 C140 12 280 14 417 26 L417 30 L0 30Z" fill="var(--slate)"/>
  </svg>
</section>

<section class="piece envelope-front" aria-label="Envelope front">
  <div class="wordmark">talvora<span class="dot"></span></div>
  <div class="address">2140 Harbor Way- Suite 310<br>Oakland, CA 94607</div>
  <svg class="wave" viewBox="0 0 466 32" height="32" preserveAspectRatio="none">
    <path d="M0 14 C150 -4 320 -2 466 24 L466 32 L0 32Z" fill="var(--blue)"/>
    <path d="M0 22 C160 4 330 6 466 28 L466 32 L0 32Z" fill="var(--silver)"/>
    <path d="M0 27 C170 10 340 12 466 32 L0 32Z" fill="var(--slate)"/>
  </svg>
</section>

<section class="piece envelope-back" aria-label="Envelope back">
  <svg class="flap" viewBox="0 0 466 110" preserveAspectRatio="none">
    <path d="M0 0 L466 0 L450 110 L16 110Z" fill="var(--slate)"/>
  </svg>
  <div class="wordmark">talvora</div>
</section>

<section class="piece card-back" aria-label="Business card back">
  <div class="wordmark">talvora<span class="dot"></span></div>
</section>

<section class="piece card-front" aria-label="Business card front">
  <div class="wordmark">talvora<span class="dot"></span></div>
  <div class="hq">Bay Area HQ<br>2140 Harbor Way<br>Suite 310<br>Oakland, CA 94607</div>
  <div class="divider"></div>
  <div class="person">
    <div class="name">MAYA LINDQVIST</div>
    <div class="role">Account Executive</div>
    <div class="contact">
      <div class="row"><span class="icon"></span>(415) 555-0142</div>
      <div class="row"><span class="icon"></span>info@talvora-advisory.com</div>
      <div class="row"><span class="icon"></span>www.talvora-advisory.com</div>
    </div>
  </div>
  <svg class="wave" viewBox="0 0 173 10" height="10" preserveAspectRatio="none">
    <path d="M0 5 C60 -1 120 0 173 7 L173 10 L0 10Z" fill="var(--blue)"/>
    <path d="M0 8 C60 3 120 4 173 9 L173 10 L0 10Z" fill="var(--silver)"/>
  </svg>
</section>

</body>
</html>
```